We are wanting a designer to design an ebook on Residential Property in Australia. This ebook is a quarterly report and covers 5 major capital cities in Australia. This is the first quarterly report for the year - another 3 are needed to be created. If you are chosen as our designer please expect ongoing work which is well rewarded.

To begin with:

We will only need you to design a few pages so we can see your style. Then if you are chosen we will get you to do the whole thing.

Can you please design the title page, page 5 and the Adelaide section(page 6 & 7) of the The Housing Market Horizon - Seasonal Capital Bulletin - Q1 2014 document attached.

The ebook brief:

You will need to create 2 graphs to include in the ebook from the data I give to you for each capital city (one graph for houses and one graph for units).

We already have a style of ebook in mind from a previous ebook our in-office designer has created for our company. You will need to keep with the logo/style/colours/fonts etc. We are looking for a designer based in Australia.

Sources and content:

Below I have shared a dropbox folder with you. It contains the first ebook our designer has created for you to view the style,logo etc - FundWise-Estate-ebook. The folder also contains the source files for the logo.

https://www.filecrate-share.com/sh/4k2pzw7rt5qn1vx/BBQ418tuwpl93GHNRMKE_zqrb#/

The Housing Market Horizon - Seasonal Capital Bulletin - Q1 2014 document attached is the content we need made into the ebook.

Each page has been set out with the content needed for that page. Each capital city content spreads out over two pages with a graph on each. I have highlighted in red the data needed to create each of the graphs. The graph style must look like the Market Outlook image in the shared dropbox folder.

You will also need to redesign the graph on page 5. You may do this how you like as long as it keeps in the style of the ebook. We will also need the source files on this ebook.

Industry/Entity Type

Investment

```html
<!DOCTYPE html>
<html lang="en">
<head>
<meta charset="utf-8">
<title>Adelaide – Market Review</title>
<link href="https://fonts.googleapis.com/css2?family=Open+Sans:wght@400;600;700&display=swap" rel="stylesheet">
<style>
  :root {
    --brand-red: #c8202f;
    --brand-red-dark: #a8141f;
    --ink: #1f1f1f;
    --chart-blue: #1f5f93;
    --grid-pink: #f3c3c8;
    --label-grey: #666;
    --green: #3a9a3a;
    --purple: #7a3a9a;
    --orange: #f07d1a;
    --paper: #ffffff;
  }
  * { margin: 0; padding: 0; box-sizing: border-box; }
  html, body { width: 848px; height: 1200px; overflow: hidden; background: var(--paper); }
  body { font-family: "Open Sans", Arial, sans-serif; color: var(--ink); position: relative; }

  .page-header {
    position: absolute; left: 0; top: 28px; width: 848px; height: 86px;
    background: var(--brand-red);
  }
  .city-title {
    position: absolute; left: 26px; top: 36px;
    font-size: 44px; font-weight: 700; color: #fff; letter-spacing: 0.5px;
  }
  .region-icon {
    position: absolute; right: 30px; top: 40px; width: 58px; height: 50px;
    background: rgba(255,255,255,0.85); border-radius: 6px;
  }
  .hero-photo {
    position: absolute; left: 0; top: 114px; width: 848px; height: 339px;
    background: linear-gradient(180deg, #3a86d0 0%, #8ec2ee 45%, #b9cfd6 62%, #5f8a4c 78%, #6a8a9a 100%);
  }
  .divider-band {
    position: absolute; left: 0; top: 453px; width: 848px; height: 57px;
    background: var(--brand-red);
  }

  .review-heading {
    position: absolute; left: 46px; top: 528px;
    font-size: 34px; font-weight: 700; color: var(--brand-red);
  }
  .review-body {
    position: absolute; left: 46px; top: 590px; width: 760px;
    font-size: 16.4px; font-weight: 700; line-height: 24px; color: var(--ink);
  }
  .review-body p { margin-bottom: 24px; }

  .outlook-heading {
    position: absolute; left: 146px; top: 822px;
    font-size: 27px; font-weight: 600; color: var(--brand-red);
  }
  .outlook-sub {
    position: absolute; left: 147px; top: 856px;
    font-size: 13.5px; color: var(--chart-blue);
  }

  .outlook-panel {
    position: absolute; left: 147px; top: 884px; width: 551px; height: 285px;
    border: 1.5px solid var(--brand-red);
  }
  .stat-grid {
    display: grid; grid-template-columns: 195px 192px 1fr; grid-template-rows: 42px 42px;
  }
  .stat {
    display: flex; align-items: center; padding-left: 12px;
    border-right: 1.5px solid var(--brand-red); border-bottom: 1.5px solid var(--brand-red);
  }
  .stat:nth-child(3n) { border-right: none; }
  .stat svg { width: 22px; height: 22px; flex: none; }
  .stat-label {
    font-size: 9.5px; font-weight: 700; line-height: 10px; text-align: right;
    margin: 0 8px 0 6px; width: 48px;
  }
  .stat-value { font-size: 22px; color: var(--chart-blue); letter-spacing: -0.5px; }
  .label-red { color: var(--brand-red); }
  .label-green { color: var(--green); }
  .label-purple { color: var(--purple); }
  .label-dark { color: var(--ink); }
  .label-orange { color: var(--orange); }

  .trend-chart { position: absolute; left: 0; top: 84px; width: 548px; height: 198px; }
  .trend-chart text { font-family: "Open Sans", Arial, sans-serif; fill: var(--label-grey); }

  .brand-mark {
    position: absolute; left: 728px; top: 1096px; width: 100px;
    display: flex; align-items: center; gap: 6px;
  }
  .brand-mark .square { width: 14px; height: 14px; background: var(--brand-red); flex: none; }
  .brand-mark .name { font-size: 15px; font-weight: 700; color: var(--brand-red); }
</style>
</head>
<body>
  <header class="page-header"></header>
  <h1 class="city-title">Adelaide</h1>
  <div class="region-icon" role="img" aria-label="Outline map of Australia with South Australia marked"></div>
  <div class="hero-photo" role="img" aria-label="Adelaide skyline across the River Torrens with parkland and blue sky"></div>
  <div class="divider-band"></div>

  <h2 class="review-heading">IN REVIEW</h2>
  <div class="review-body">
    <p>The property market in South Australia is performing well and The Property Council of Southern Regions (PCSR) anticipate that positive growth for the state will continue into 2014.</p>
    <p>Looking at median house price data for the previous 12 months, Adelaide showed an encouraging increase of 2.8 per cent with the median house price now sitting at $407,500. According to PCSR President, Mr Neil Carrow, “This is the first time in almost three years that the median price has crossed the $400,000 threshold.”</p>
    <p>Adelaide’s unit market is also up by 2.56 per cent with a current median value of $305,000</p>
  </div>

  <h2 class="outlook-heading">2014 MARKET OUTLOOK - HOMES</h2>
  <div class="outlook-sub">Median values of Adelaide for the current quarter.</div>

  <section class="outlook-panel">
    <div class="stat-grid">
      <div class="stat">
        <svg viewBox="0 0 22 22"><circle cx="11" cy="11" r="10" fill="#c8202f"/><text x="11" y="16" text-anchor="middle" font-size="14" font-weight="700" fill="#fff" font-family="Arial, sans-serif">$</text></svg>
        <span class="stat-label label-red">UNIT<br>VALUE</span><span class="stat-value">$407,500</span>
      </div>
      <div class="stat">
        <svg viewBox="0 0 22 22"><circle cx="11" cy="8" r="7" fill="#3a9a3a"/><rect x="10" y="12" width="2" height="9" fill="#3a9a3a"/></svg>
        <span class="stat-label label-green">CAPITAL<br>GROWTH</span><span class="stat-value">2.65%</span>
      </div>
      <div class="stat">
        <svg viewBox="0 0 22 22" fill="#7a3a9a"><rect x="2" y="15" width="3" height="5"/><rect x="7" y="11" width="3" height="9"/><rect x="12" y="7" width="3" height="13"/><rect x="17" y="3" width="3" height="17"/></svg>
        <span class="stat-label label-purple">RENTAL<br>YIELD</span><span class="stat-value">4.66%</span>
      </div>
      <div class="stat">
        <svg viewBox="0 0 22 22" fill="#1f1f1f"><path d="M11 2 L21 11 H18 V20 H13 V14 H9 V20 H4 V11 H1 Z"/></svg>
        <span class="stat-label label-dark">UNIT<br>SALES</span><span class="stat-value">5,059</span>
      </div>
      <div class="stat">
        <svg viewBox="0 0 22 22"><rect x="2" y="4" width="18" height="16" rx="1" fill="#f07d1a"/><rect x="4" y="9" width="14" height="9" fill="#fff"/><rect x="6" y="2" width="2" height="4" fill="#f07d1a"/><rect x="14" y="2" width="2" height="4" fill="#f07d1a"/></svg>
        <span class="stat-label label-orange">WEEKLY<br>RENT</span><span class="stat-value">$365</span>
      </div>
      <div class="stat">
        <svg viewBox="0 0 22 22" fill="none" stroke="#1f1f1f" stroke-width="2"><path d="M4 12 V8 H17"/><path d="M14 5 L17 8 L14 11"/><path d="M18 10 V14 H5"/><path d="M8 11 L5 14 L8 17"/></svg>
        <span class="stat-label label-dark">TOTAL<br>RETURN</span><span class="stat-value">1.87%</span>
      </div>
    </div>

    <svg class="trend-chart" viewBox="0 0 548 198" aria-label="Line chart of Adelaide median home values, December 2003 to December 2013">
      <text x="530" y="22" text-anchor="end" font-size="8">Median Value - Adelaide Homes</text>
      <g stroke="var(--grid-pink)" stroke-width="0.8">
        <line x1="58" y1="40" x2="524" y2="40"/><line x1="58" y1="68.5" x2="524" y2="68.5"/>
        <line x1="58" y1="97" x2="524" y2="97"/><line x1="58" y1="125.5" x2="524" y2="125.5"/>
        <line x1="58" y1="154" x2="524" y2="154"/>
        <line x1="61" y1="34" x2="61" y2="158"/><line x1="84" y1="34" x2="84" y2="158"/><line x1="107" y1="34" x2="107" y2="158"/><line x1="130" y1="34" x2="130" y2="158"/><line x1="153" y1="34" x2="153" y2="158"/><line x1="176" y1="34" x2="176" y2="158"/><line x1="199" y1="34" x2="199" y2="158"/><line x1="222" y1="34" x2="222" y2="158"/><line x1="245" y1="34" x2="245" y2="158"/><line x1="268" y1="34" x2="268" y2="158"/><line x1="291" y1="34" x2="291" y2="158"/><line x1="314" y1="34" x2="314" y2="158"/><line x1="337" y1="34" x2="337" y2="158"/><line x1="360" y1="34" x2="360" y2="158"/><line x1="383" y1="34" x2="383" y2="158"/><line x1="406" y1="34" x2="406" y2="158"/><line x1="429" y1="34" x2="429" y2="158"/><line x1="452" y1="34" x2="452" y2="158"/><line x1="475" y1="34" x2="475" y2="158"/><line x1="498" y1="34" x2="498" y2="158"/><line x1="521" y1="34" x2="521" y2="158"/>
      </g>
      <g font-size="8">
        <text x="14" y="43">$450,000</text><text x="14" y="71.5">$400,000</text>
        <text x="14" y="100">$350,000</text><text x="14" y="128.5">$300,000</text>
        <text x="14" y="157">$250,000</text>
      </g>
      <polyline fill="none" stroke="var(--chart-blue)" stroke-width="1.8"
        points="61,154 84,149.4 107,144.3 130,139.8 153,136.9 176,132.4 199,127.8 222,114.1 245,94.2 268,82.8 291,88.5 314,79.9 337,69.7 360,64.5 383,64.5 406,68.5 429,74.2 452,75.4 475,75.4 498,72.5 521,64.2"/>
      <g fill="#fff" stroke="var(--chart-blue)" stroke-width="1.6">
        <circle cx="61" cy="154" r="3"/><circle cx="84" cy="149.4" r="3"/><circle cx="107" cy="144.3" r="3"/><circle cx="130" cy="139.8" r="3"/><circle cx="153" cy="136.9" r="3"/><circle cx="176" cy="132.4" r="3"/><circle cx="199" cy="127.8" r="3"/><circle cx="222" cy="114.1" r="3"/><circle cx="245" cy="94.2" r="3"/><circle cx="268" cy="82.8" r="3"/><circle cx="291" cy="88.5" r="3"/><circle cx="314" cy="79.9" r="3"/><circle cx="337" cy="69.7" r="3"/><circle cx="360" cy="64.5" r="3"/><circle cx="383" cy="64.5" r="3"/><circle cx="406" cy="68.5" r="3"/><circle cx="429" cy="74.2" r="3"/><circle cx="452" cy="75.4" r="3"/><circle cx="475" cy="75.4" r="3"/><circle cx="498" cy="72.5" r="3"/>
      </g>
      <circle cx="521" cy="64.2" r="3.6" fill="#fff" stroke="var(--brand-red)" stroke-width="1.8"/>
      <g font-size="7.5" text-anchor="middle">
        <text x="61" y="170">DEC</text><text x="84" y="170">JUN</text><text x="107" y="170">DEC</text><text x="130" y="170">JUN</text><text x="153" y="170">DEC</text><text x="176" y="170">JUN</text><text x="199" y="170">DEC</text><text x="222" y="170">JUN</text><text x="245" y="170">DEC</text><text x="268" y="170">JUN</text><text x="291" y="170">DEC</text><text x="314" y="170">JUN</text><text x="337" y="170">DEC</text><text x="360" y="170">JUN</text><text x="383" y="170">DEC</text><text x="406" y="170">JUN</text><text x="429" y="170">DEC</text><text x="452" y="170">JUN</text><text x="475" y="170">DEC</text><text x="498" y="170">JUN</text><text x="521" y="170">DEC</text>
        <text x="61" y="181">2003</text><text x="84" y="181">2004</text><text x="107" y="181">2004</text><text x="130" y="181">2005</text><text x="153" y="181">2005</text><text x="176" y="181">2006</text><text x="199" y="181">2006</text><text x="222" y="181">2007</text><text x="245" y="181">2007</text><text x="268" y="181">2008</text><text x="291" y="181">2008</text><text x="314" y="181">2009</text><text x="337" y="181">2009</text><text x="360" y="181">2010</text><text x="383" y="181">2010</text><text x="406" y="181">2011</text><text x="429" y="181">2011</text><text x="452" y="181">2012</text><text x="475" y="181">2012</text><text x="498" y="181">2013</text><text x="521" y="181">2013</text>
      </g>
    </svg>
  </section>

  <div class="brand-mark"><span class="square"></span><span class="name">FundWise</span></div>
</body>
</html>
```